Brochure for a website accessibility report

This brochure is related to a report that www.qelvantrix.org sell. The report shows the results of an automated audit of a websites accessibility. It shows details of issues found with screen shots, examples of code and provides remediation advice.

The brochure will be a pdf 8.5 inches by 11 inches. It can be anywhere from 6 to 10 pages.

The FlintVue™ name itself should be “Bree Serif” font. The fonts, styles, colors and sizes are up to you.

The images used and logo of the Office of Digital Reachworks and K7P logo are upload

We highlighted in blue page extracts from the report we sell. Do not use the blue highlight, it is merely there to show you where the specific examples of the report we sell are vs the other content in the report. The areas in blue which show the content from the actual report should be shown as an extract of the actual page of the report. You have flexibility to change the layout and the way the content look.

The red square callouts over the blue content are callouts that describe the specific page extracts. We used it as a red callout only so that you would be able to see it. You should change the specific location, look and feel of the callout to be appropriate

Target Market(s)

Marketing and Technical people

Industry/Entity Type

Information Technology

Font styles to use
Sans Serif

Colors

Designer to choose colors to be used in the design.

Requirements
Should not have
• wheelchairs, images of blind people

```html
<!DOCTYPE html>
<html lang="en">
<head>
<meta charset="utf-8">
<title>Section 2 – Developer Guide</title>
<link href="https://fonts.googleapis.com/css2?family=Bree+Serif&family=Roboto:wght@300;400;500;700&display=swap" rel="stylesheet">
<style>
  :root {
    --page-bg: #f8f5f1;
    --brand-green: #1fae6a;
    --ink-dark: #2f4a3c;
    --ink-body: #555a57;
    --card-bg: #fff3e3;
    --accent-gold: #e3c48e;
    --checkpoint: #e2bd83;
  }
  * { box-sizing: border-box; margin: 0; padding: 0; }
  html, body { width: 927px; height: 1200px; overflow: hidden; }
  body {
    position: relative;
    background: var(--page-bg);
    font-family: "Roboto", Arial, sans-serif;
    font-weight: 300;
    color: var(--ink-body);
  }
  .block { position: absolute; left: 51px; width: 825px; }
  .section-title {
    top: 78px;
    font-family: "Bree Serif", Georgia, serif;
    font-weight: 400;
    font-size: 30px;
    color: var(--brand-green);
  }
  .body-text { font-size: 15.3px; line-height: 20px; text-align: justify; }
  .intro { top: 129px; }
  .themes { top: 189px; }
  .theme { display: flex; height: 40.3px; font-size: 15.3px; line-height: 20px; }
  .theme dt { width: 88px; font-weight: 500; color: var(--ink-dark); }
  .theme dd { flex: 1; }
  .details { top: 436px; }
  .remediation { top: 495px; }
  .callout {
    position: absolute; top: 580px; left: 82px; width: 780px;
    font-size: 17px; line-height: 22px; font-weight: 500;
    color: var(--brand-green);
  }
  .theme-card {
    position: absolute; top: 670px; left: 52px; width: 824px; height: 600px;
    background: var(--card-bg);
    border-radius: 42px;
    box-shadow: 0 2px 14px rgba(0,0,0,0.12);
    padding: 44px 51px 0 52px;
  }
  .card-title {
    font-family: "Bree Serif", Georgia, serif;
    font-weight: 400; font-size: 32px; line-height: 38px;
    color: var(--brand-green);
  }
  .card-intro { margin-top: 10px; font-size: 15.3px; line-height: 20px; }
  .card-list { list-style: none; margin-top: 20px; }
  .card-list li {
    position: relative; padding-left: 29px;
    font-size: 15.3px; line-height: 20px; margin-bottom: 20px;
  }
  .card-list li::before {
    content: ""; position: absolute; left: 3px; top: 7px;
    width: 5px; height: 5px; background: var(--accent-gold);
  }
  .issue-label { margin-top: 17px; font-size: 14px; line-height: 20px; font-weight: 500; color: var(--ink-dark); }
  .issue-label span { color: var(--brand-green); }
  .issue-text { font-size: 15.3px; line-height: 25px; text-align: justify; }
  .issue-text + .issue-text { margin-top: 4px; }
  .checkpoints { font-size: 15.3px; line-height: 25px; }
  .checkpoints span { color: var(--checkpoint); margin-left: 18px; }
</style>
</head>
<body>
  <h1 class="block section-title">SECTION 2</h1>

  <p class="block body-text intro">The next section of the report is designed specifically for your developers and programmers who will be in-thet­renches fixing the actual issues. The issues are prioritized and organized by six themes:</p>

  <dl class="block themes">
    <div class="theme"><dt>Media:</dt><dd>Problems related to imagery, video and plug-ins.</dd></div>
    <div class="theme"><dt>Structure:</dt><dd>Problems related to HTML layout markup and positioning of data.</dd></div>
    <div class="theme"><dt>Text:</dt><dd>Problems related to actual textual content and its comprehension.</dd></div>
    <div class="theme"><dt>Scripting:</dt><dd>Problems related to Scripting. e.g. in JavaScript code.</dd></div>
    <div class="theme"><dt>CSS:</dt><dd>Problems related to Cascading Style Sheets &amp; inline Styles.</dd></div>
    <div class="theme"><dt>Form:</dt><dd>Problems related to Form controls, navigability &amp; comprehension.</dd></div>
  </dl>

  <p class="block body-text details">Within each classification above, we provide specific details about each violation found, which URLs they were present on, code snippets, and screenshots showing you the actual violation.</p>

  <p class="block body-text remediation">Remediation advice is then given to you with resource links and explanations of the guidelines your website doesn’t meet.</p>

  <p class="callout">The following pages provide six examples of how our FlintVue™ report shows you how to fix the violations based on the classifications listed above.</p>

  <section class="theme-card">
    <h2 class="card-title">Media</h2>
    <p class="card-intro">Ensure that all Media items such as animations/video and audio have an alternative means of understanding the content.</p>
    <ul class="card-list">
      <li>Provide a text alternative for either via a transcript, audio description, sign language, or caption­ing (open or closed.)</li>
      <li>Additionally, any content provided through an object, Embed, or Applet (or similar 3rd party-plugin) must be checked for appropriate keyboard accessible controls.</li>
    </ul>
    <p class="issue-label">ISSUE: <span>IMAGE LINK TEXT&nbsp; (PRIORITY 2)</span></p>
    <p class="issue-text">Image ALT attribute text of images within links should not duplicate the text of the link body (link text.).</p>
    <p class="issue-text">Don't use the same text in an image ALT as the link containing the image. If the link text and the image alt are the same, this creates a "stutter" when screen readers read the content of the link and then the image. When the image doesn't describe any additional information beyond the link text, authors should set the image alt to "".</p>
    <p class="checkpoints">Issue is relevant to checkpoints: <span>1.1.1 (A),</span> <span>2.4.4 (A),</span> <span>4.1.2 (A)</span></p>
  </section>
</body>
</html>
```